Tinker's Lamp sports bar beer & food menu

We need a menu design for our gastropub sports bar in L.A.'s Sawtelle Neighborhood (Little Osaka). We have a full-bar (hard liquor, craft beer, wine and cocktails) . We have a lunch and dinner menu as well as a happy hour menu. On Sundays we have a seperate menu with brunch items. The design concept is a British pub type of sports bar. We're looking for something different from our existing menu design. Ideally something cleaner and more legible. It should mesh a simple, modern sensibility with the more traditional darkened pub style of our interior design.

You can check out our Voxly page for photos of the interior/exterior:
https://www.reviewhatch.example/biz_photos/tinkers-lamp-los-angeles?tab=interior

You can view our existing menu here:
https://www.reviewhatch.example/biz_photos/tinkers-lamp-los-angeles?tab=menu

If there's an area of the design that can be a little more playful it's our highlighted event schedule so that the events will stand out.

Target Market(s)

Age of 25 and up. Sawtelle is a cultural hub that caters to a younger, moderately affluent crowd.

Industry/Entity Type

Sports Bar

Font styles to use
Sans Serif

Colors

Designer to choose colors to be used in the design.

Requirements
Must have
• Logo, highlighted event schedule (beer pong Monday, trivia Tuesday, taco Tuesday, whiskey Wednesday, karaoke Saturday). The menu should be easy to read in a darkened bar. We'll be printing on standard 8.5x11 in portrait.
Nice to have
• We're trying to have the menu take up as few pages as possible.
Should not have
• We're trying to have the menu take up as few pages as possible. Food photography isn't necessary. A cover isn't necessary. Please avoid clip art of food.

```html
<!DOCTYPE html>
<html lang="en">
<head>
<meta charset="utf-8">
<title>Tinker's Lamp — Menu</title>
<link rel="stylesheet" href="https://fonts.googleapis.com/css2?family=Archivo+Black&family=Abril+Fatface&family=Karla:wght@400;500&family=Work+Sans:wght@500;600&display=swap">
<style>
  :root {
    --navy: #26408b;
    --amber: #f9b13f;
    --ink: #141414;
    --paper: #ffffff;
  }
  * { margin: 0; padding: 0; box-sizing: border-box; }
  html, body { width: 927px; height: 1200px; overflow: hidden; }
  body { background: var(--navy); font-family: "Karla", sans-serif; color: var(--ink); }

  .menu { position: relative; width: 927px; height: 1200px; background: var(--navy); }
  .sheet {
    position: absolute;
    left: 30px; top: 30px;
    width: 867px; height: 1139px;
    background: var(--paper);
  }

  .section { position: absolute; }
  .col-left { left: 59px; width: 350px; }
  .col-right { left: 444px; width: 356px; }

  .section-title {
    font-family: "Archivo Black", sans-serif;
    font-size: 34px;
    line-height: 36px;
    letter-spacing: 0.3px;
    color: transparent;
    -webkit-text-stroke: 1.2px var(--ink);
    text-shadow: -2.5px 2.5px 0 var(--amber);
    margin-bottom: 6px;
    white-space: nowrap;
  }
  .section-title.small {
    font-size: 18px;
    line-height: 20px;
    -webkit-text-stroke: 0.8px var(--ink);
    text-shadow: -1.5px 1.5px 0 var(--amber);
    margin-bottom: 2px;
  }

  .item { margin-bottom: 22px; }
  .item-name {
    font-family: "Work Sans", sans-serif;
    font-weight: 600;
    font-size: 14.5px;
    line-height: 21px;
    letter-spacing: 0.6px;
    text-transform: uppercase;
    white-space: nowrap;
  }
  .dollar { font-weight: 500; }
  .price { font-family: "Abril Fatface", serif; font-size: 21px; line-height: 14px; }
  .size {
    font-family: "Work Sans", sans-serif;
    font-weight: 500;
    font-size: 10.5px;
    letter-spacing: 0.8px;
    margin-left: 4px;
  }
  .price + .size { margin-left: 8px; }
  .item-desc { font-size: 14.2px; line-height: 21px; letter-spacing: 0.4px; }
  .item-note {
    font-family: "Work Sans", sans-serif;
    font-size: 10px;
    line-height: 22px;
    letter-spacing: 0.5px;
    text-transform: uppercase;
  }

  .addons-list {
    font-family: "Work Sans", sans-serif;
    font-weight: 600;
    font-size: 12.5px;
    letter-spacing: 0.5px;
    line-height: 22px;
    white-space: nowrap;
  }
  .addons-list .price { font-size: 18px; }
  .addons-list .sep { color: var(--amber); font-weight: 500; margin: 0 3px; }

  .events {
    position: absolute;
    left: 444px; top: 703px;
    width: 364px; height: 377px;
    border: 7px solid var(--amber);
  }
  .events-brand {
    position: absolute;
    left: 40px; top: -28px;
    width: 270px; height: 50px;
    background: var(--paper);
    display: flex; align-items: center; justify-content: center; gap: 10px;
  }
  .brand-mark { width: 20px; height: 20px; background: var(--amber); }
  .brand-name {
    font-family: "Work Sans", sans-serif;
    font-weight: 600;
    font-size: 28px;
    color: var(--ink);
    white-space: nowrap;
  }
  .events-title {
    position: absolute;
    left: 0; right: 0; top: 50px;
    text-align: center;
    font-family: "Archivo Black", sans-serif;
    font-size: 34px;
    line-height: 36px;
    letter-spacing: 0.3px;
    color: transparent;
    -webkit-text-stroke: 1.2px var(--ink);
    text-shadow: -2.5px 2.5px 0 var(--amber);
  }
  .events-list {
    position: absolute;
    left: 0; right: 0; top: 150px;
    list-style: none;
    text-align: center;
  }
  .events-list li {
    height: 42.3px;
    font-family: "Work Sans", sans-serif;
    font-weight: 600;
    font-size: 15px;
    letter-spacing: 0.8px;
    line-height: 21px;
  }
  .events-list .day { color: var(--navy); font-weight: 500; }
</style>
</head>
<body>
<main class="menu">
  <div class="sheet">

    <section class="section col-left" style="top:69px">
      <h2 class="section-title">FOR THE TABLE</h2>
      <div class="item">
        <div class="item-name">Tinker's 3 Whole Wings <span class="dollar">$</span><span class="price">9</span></div>
        <div class="item-desc">Choice of Dry Rub, Sweet N' Spicy or Buffalo</div>
      </div>
      <div class="item">
        <div class="item-name">Brussel Sprouts <span class="dollar">$</span><span class="price">8</span></div>
        <div class="item-desc">Sautéed with Chorizo, Roasted Almonds &amp; Golden Raisins</div>
      </div>
      <div class="item">
        <div class="item-name">Golden Calamari <span class="dollar">$</span><span class="price">11</span></div>
        <div class="item-desc">Traditionally Served with Spiced Marinara</div>
      </div>
      <div class="item">
        <div class="item-name">Shrimp Mac N' Cheese <span class="dollar">$</span><span class="price">12</span></div>
        <div class="item-desc">Baked with Fontina, Sharp Cheddar &amp; Parmesan</div>
      </div>
      <div class="item">
        <div class="item-name">1/2 Dozen Oysters <span class="dollar">$</span><span class="price">12</span></div>
        <div class="item-desc">Kestrel Bay's Served with Our Own Mignonette</div>
      </div>
      <div class="item">
        <div class="item-name">Charcuterie <span class="dollar">$</span><span class="price">15</span></div>
        <div class="item-desc">Seasonal Meats &amp; Cheese</div>
      </div>
      <div class="item">
        <div class="item-name">Nachos <span class="dollar">$</span><span class="price">9</span></div>
        <div class="item-desc">Medley of Black Beans, Pico De Gallo, Cheese, Jalapeno &amp; Sour Cream</div>
      </div>
      <div class="item">
        <div class="item-name">Mozzarella Cheese Sticks <span class="dollar">$</span><span class="price">9</span></div>
      </div>
    </section>

    <section class="section col-left" style="top:673px">
      <h2 class="section-title">SIDES</h2>
      <div class="item"><div class="item-name">House Fries <span class="dollar">$</span><span class="price">6</span></div></div>
      <div class="item"><div class="item-name">Dry Rub Fries <span class="dollar">$</span><span class="price">6</span></div></div>
      <div class="item"><div class="item-name">Truffle Fries <span class="dollar">$</span><span class="price">7</span></div></div>
      <div class="item"><div class="item-name">Sweet Potato Fries <span class="dollar">$</span><span class="price">6</span></div></div>
    </section>

    <section class="section col-left" style="top:907px">
      <h2 class="section-title">DESSERTS</h2>
      <div class="item"><div class="item-name">Coco Flan <span class="dollar">$</span><span class="price">9</span></div></div>
      <div class="item"><div class="item-name">Cheese Cake <span class="dollar">$</span><span class="price">9</span></div></div>
      <div class="item"><div class="item-name">Peach Tart <span class="dollar">$</span><span class="price">9</span></div></div>
    </section>

    <section class="section col-right" style="top:69px">
      <h2 class="section-title">SALADS &amp; SOUPS</h2>
      <div class="item">
        <div class="item-name">Chili Soup<span class="size">CUP</span> <span class="dollar">$</span><span class="price">7</span><span class="size">BOWL</span> <span class="dollar">$</span><span class="price">9</span></div>
        <div class="item-desc">Turkey with Vegetables, Onions &amp; Sharp Cheddar</div>
      </div>
      <div class="item">
        <div class="item-name">Soup of the Day<span class="size">CUP</span> <span class="dollar">$</span><span class="price">5</span><span class="size">BOWL</span> <span class="dollar">$</span><span class="price">7</span></div>
      </div>
      <div class="item">
        <div class="item-name">Caesar <span class="dollar">$</span><span class="price">10</span></div>
        <div class="item-desc">Romaine Hearts, Croutons &amp; Shaved Parmesan</div>
      </div>
      <div class="item">
        <div class="item-name">Tinker's Lamp Chopped Salad <span class="dollar">$</span><span class="price">11</span></div>
        <div class="item-desc">Romaine, Salami, Provolone, Banana Peppers, Red Onions, Olives, Garbanzos Tomatoes, Celery, Tossed in a Red Wine Vinaigrette</div>
      </div>
      <div class="item">
        <div class="item-name">Southwest Salad <span class="dollar">$</span><span class="price">12</span></div>
        <div class="item-desc">Romaine, Tomato, Corn, Avocado, Tossed with a Jalapeno Cilantro Vinaigrette</div>
        <div class="item-note">Garnished with tortilla chips, cheddar &amp; sour cream</div>
      </div>
      <div class="item">
        <div class="item-name">Quinoa Salad <span class="dollar">$</span><span class="price">12</span></div>
        <div class="item-desc">Roasted Beets, Asparagus, Brussel Sprouts, Mushrooms, Kale, Watermelon Radish, Tossed in a Citrus Vinaigrette</div>
      </div>
    </section>

    <section class="section col-right" style="top:601px">
      <h3 class="section-title small">ADD ONS</h3>
      <div class="addons-list">
        CHICKEN <span class="dollar">$</span><span class="price">4</span><span class="sep">|</span>
        SHRIMP <span class="dollar">$</span><span class="price">6</span><span class="sep">|</span>
        SALMON <span class="dollar">$</span><span class="price">6</span><span class="sep">|</span>
        STEAK <span class="dollar">$</span><span class="price">9</span>
      </div>
    </section>

    <section class="events">
      <div class="events-brand">
        <span class="brand-mark"></span>
        <span class="brand-name">Tinker's Lamp</span>
      </div>
      <h2 class="events-title">EVENTS<br>SCHEDULE</h2>
      <ul class="events-list">
        <li>BEER PONG <span class="day">MONDAY</span></li>
        <li>TRIVIA <span class="day">TUESDAY</span></li>
        <li>TACO <span class="day">TUESDAY</span></li>
        <li>WHISKEY <span class="day">WEDNESDAY</span></li>
        <li>KARAOKE <span class="day">SATURDAY</span></li>
      </ul>
    </section>

  </div>
</main>
</body>
</html>
```